Cedar & Stone Subtitle Walking Toward the Quiet Dawn

This is a spiritual book. It opens with a question for the readers -- Are you happy? Then proceeds to discuss the meaning of happiness, why the majority isn't and ways to achieve it. The work offers hope, and actual answers. In that regard the cover needs to relate those things.

I'm happy to contribute by answering further questions and making suggestions, however, am open to the designer letting their Spirit soar and see where it leads them.

Ask yourself the question; Am I happy, imagine finding Your happiness then designing the cover that comes from that space. Just a thought.

```html
<!DOCTYPE html>
<html lang="en">
<head>
<meta charset="utf-8">
<title>Cedar &amp; Stone — Book Cover</title>
<link href="https://fonts.googleapis.com/css2?family=Cinzel:wght@400;500&family=Open+Sans:wght@400;700&display=swap" rel="stylesheet">
<style>
  :root {
    --ink: #221e1c;
    --paper: #ffffff;
    --page-bg: #ffffff;
    --spine-line: #6d6966;
    --title-ink: #1c1917;
  }
  * { margin: 0; padding: 0; box-sizing: border-box; }
  html, body {
    width: 1200px;
    height: 1000px;
    overflow: hidden;
    background: var(--page-bg);
  }
  .cover-spread {
    position: absolute;
    left: 200px;
    top: 215px;
    width: 800px;
    height: 570px;
    background: var(--paper);
    box-shadow: 2px 4px 10px rgba(0,0,0,0.22);
  }
  .cover-shapes {
    position: absolute;
    inset: 0;
    width: 800px;
    height: 570px;
  }
  .cover-shapes .fill-ink { fill: var(--ink); }
  .cover-shapes .fill-paper { fill: var(--paper); }
  .cover-shapes .spine-line { stroke: var(--spine-line); stroke-width: 0.8; }

  .title {
    position: absolute;
    left: 400px;
    width: 400px;
    text-align: center;
    font-family: "Cinzel", serif;
    color: var(--title-ink);
    line-height: 1;
  }
  .title-main { top: 70px; font-size: 50px; font-weight: 400; letter-spacing: 1px; }
  .title-amp { top: 171px; font-size: 20px; }
  .title-second { top: 200px; font-size: 26px; font-weight: 400; letter-spacing: 1px; }

  .subtitle {
    position: absolute;
    left: 466px;
    top: 496px;
    font-family: "Open Sans", sans-serif;
    font-size: 13px;
    color: var(--paper);
    word-spacing: 4px;
    white-space: nowrap;
  }
  .subtitle strong { font-weight: 700; }

  .author {
    position: absolute;
    right: 22px;
    top: 534px;
    font-family: "Open Sans", sans-serif;
    font-size: 13px;
    letter-spacing: 2px;
    color: var(--paper);
    text-transform: uppercase;
  }

  .back-word {
    position: absolute;
    font-family: "Open Sans", sans-serif;
    color: var(--ink);
    line-height: 1;
    white-space: nowrap;
    transform-origin: center;
  }
  .back-word--etc { left: 6px; top: 412px; font-size: 14px; transform: rotate(-28deg); }
  .back-word--family { left: 1px; top: 470px; font-size: 16px; transform: rotate(38deg); }
  .back-word--career { left: 4px; top: 533px; font-size: 16px; transform: rotate(-38deg); }
</style>
</head>
<body>
  <div class="cover-spread">
    <svg class="cover-shapes" viewBox="0 0 800 570" aria-hidden="true">
      <polygon class="fill-ink" points="0,0 400,0 400,545.6 380,570 0,570"/>
      <polygon class="fill-paper" points="0,200 65,570 0,570"/>
      <polygon class="fill-ink" points="398,0 403,0 480,448 400,545.6 398,545.6"/>
      <polygon class="fill-ink" points="487,454 800,454 800,570 427,570"/>
      <line class="spine-line" x1="400.5" y1="0" x2="400.5" y2="545"/>
    </svg>

    <span class="back-word back-word--etc">etc</span>
    <span class="back-word back-word--family">family</span>
    <span class="back-word back-word--career">career</span>

    <h1 class="title title-main">Cedar</h1>
    <div class="title title-amp">&amp;</div>
    <div class="title title-second">Stone</div>

    <p class="subtitle">Walking Toward the <strong>Quiet</strong> <strong>Dawn</strong></p>
    <p class="author">Milo Renquist</p>
  </div>
</body>
</html>
```